Project Lists Banner for HVAC ecommerce store

We want a banner that showcases our project list feature that will allow customers to create list of products that they can select and quickly order. this will be a middle of page banner. It will replace this banner - https://www.lumapixvault.com/image/84730295
Font: Noto Sans
Size: 938x300 px
Color Options: #0059E, #00BBE3, #C6C8C7
Text:
Create lists of frequently purchased SKU's for fast ordering.
- Warehouse Inventory
- Complete Systems
- Large Projects
- And More...
"Sign In" is the call to action button. make button with non rounded (square) boarders.
We don't want a computer screen in banner nor a person. You can look at our competitors below for ideas.
Our staging server is belfarq7.com for reference
Our competitors:
https://www.brantlowholdings.com/
https://www.folvexa.com/
https://www.zelbrk.com/
https://www.vostrel.com/index.html
HVAC, B2B
HVAC

```html
<!DOCTYPE html>
<html lang="en">
<head>
<meta charset="utf-8">
<title>Project Lists Banner</title>
<link rel="stylesheet" href="https://fonts.googleapis.com/css2?family=Noto+Sans:ital,wght@0,400;0,600;0,700;1,400;1,700&display=swap">
<style>
  :root {
    --page-bg: #ffffff;
    --navy-deep: #22107a;
    --blue-royal: #0a2fd8;
    --blue-bright: #2a58f2;
    --glow-lavender: #8e98f2;
    --violet: #3d2ae0;
    --periwinkle: #6a6af8;
    --sky-soft: #5e8ff0;
    --cta: #00bbe3;
    --text-light: #ffffff;
  }
  * { margin: 0; padding: 0; box-sizing: border-box; }
  html, body {
    width: 1200px; height: 657px; overflow: hidden;
    background: var(--page-bg);
    font-family: "Noto Sans", Arial, sans-serif;
  }
  .promo-banner {
    position: absolute; left: 131px; top: 178px;
    width: 938px; height: 300px; overflow: hidden;
    color: var(--text-light);
  }
  .backdrop {
    position: absolute; inset: 0;
    background:
      radial-gradient(ellipse 280px 200px at 560px 100px, var(--glow-lavender) 0%, rgba(142,152,242,0) 100%),
      radial-gradient(ellipse 300px 240px at 900px 30px, var(--violet) 0%, rgba(61,42,224,0) 100%),
      radial-gradient(ellipse 340px 220px at 920px 300px, var(--sky-soft) 0%, rgba(94,143,240,0) 100%),
      var(--periwinkle);
  }
  .backdrop-left {
    position: absolute; inset: 0;
    background: linear-gradient(180deg, var(--blue-bright) 0%, var(--blue-royal) 35%, #1a1aa8 65%, var(--navy-deep) 92%);
    -webkit-mask: linear-gradient(90deg, #000 0%, #000 40%, transparent 62%);
            mask: linear-gradient(90deg, #000 0%, #000 40%, transparent 62%);
  }
  .headline {
    position: absolute; left: 52px; top: 28px;
    font-style: italic; font-weight: 400; text-transform: uppercase;
    letter-spacing: -0.2px;
  }
  .headline-top { display: block; font-size: 37px; line-height: 52px; }
  .headline-bottom { display: block; font-size: 37px; line-height: 54px; }
  .headline-bottom .strong { font-weight: 700; }
  .headline-bottom .sku { font-size: 45px; }
  .feature-list {
    position: absolute; left: 50px; top: 144px; list-style: none;
  }
  .feature-item {
    display: flex; align-items: center; height: 42px;
    font-weight: 600; font-size: 23px; text-transform: uppercase;
  }
  .feature-item .tail { text-transform: none; }
  .feature-icon { width: 32px; height: 28px; margin-right: 11px; fill: var(--text-light); }
  .cta-sign-in {
    position: absolute; left: 689px; top: 200px;
    width: 155px; height: 52px; border: 0; border-radius: 0;
    background: var(--cta); color: var(--text-light); text-decoration: none;
    font: 700 23px/52px "Noto Sans", Arial, sans-serif; text-align: center;
    text-transform: uppercase;
  }
</style>
</head>
<body>
  <section class="promo-banner" aria-label="Project lists promotion">
    <div class="backdrop" role="img" aria-label="Soft blue and violet abstract backdrop">
      <div class="backdrop-left"></div>
    </div>

    <h2 class="headline">
      <span class="headline-top">Create lists of&nbsp; frequently purchased</span>
      <span class="headline-bottom"><span class="strong sku">SKU'S</span> for <span class="strong">fast ordering</span></span>
    </h2>

    <ul class="feature-list">
      <li class="feature-item">
        <svg class="feature-icon" viewBox="0 0 32 28" aria-hidden="true">
          <rect x="6" y="1" width="20" height="6"/><rect x="6" y="9" width="20" height="6"/>
          <rect x="6" y="17" width="20" height="5"/><rect x="15" y="22" width="2" height="4"/>
          <rect x="6" y="25" width="20" height="2"/>
        </svg>
        Warehouse Inventory
      </li>
      <li class="feature-item">
        <svg class="feature-icon" viewBox="0 0 32 28" aria-hidden="true">
          <path d="M4 13V7h18V3l6 5-6 5V10H7v3z"/>
          <path d="M28 15v6H10v4l-6-5 6-5v3h15v-3z"/>
        </svg>
        Complete Systems
      </li>
      <li class="feature-item">
        <svg class="feature-icon" viewBox="0 0 32 28" aria-hidden="true">
          <rect x="11" y="1" width="10" height="8"/><rect x="15" y="9" width="2" height="5"/>
          <rect x="4" y="13" width="24" height="2"/><rect x="4" y="13" width="2" height="6"/>
          <rect x="26" y="13" width="2" height="6"/><rect x="15" y="13" width="2" height="6"/>
          <rect x="1" y="19" width="8" height="8"/><rect x="12" y="19" width="8" height="8"/>
          <rect x="23" y="19" width="8" height="8"/>
        </svg>
        Large Projects,&nbsp;<span class="tail">And More...</span>
      </li>
    </ul>

    <a class="cta-sign-in" href="#">Sign In</a>
  </section>
</body>
</html>
```